Healthcare and Professional IT Services Company need a redesigned business card

We are a IT Services company that targets small medical practices and professional business such as Attorneys, Accounts, Architects etc. We want to communicate a professional yet friendly image using recent logo redesign here on ArtHarbor. Like to see the colors blue and orange in the design. Must use the Tall Pine Computing as displayed in the new logo - then also want to incorporate the fish logo as well.

Target Market(s)

Small medical and professional services

Industry/Entity Type

It Company

Contact Information for Business Card

The usual stuff, place for name address phone website. Also maybe our tagline which is "rooted in computing"

Requirements
Must have
• My new logo and the fish somewhere on the card

```html
<!DOCTYPE html>
<html lang="en">
<head>
<meta charset="utf-8">
<title>Tall Pine Computing – Business Card</title>
<link href="https://fonts.googleapis.com/css2?family=Mulish:wght@400;600;800&display=swap" rel="stylesheet">
<style>
  :root {
    --blue-deep: #1477b8;
    --blue-main: #1a93d3;
    --blue-light: #22a9de;
    --orange: #e9a21e;
    --paper: #f7f7f7;
    --paper-shade: #e9e9e9;
    --ink: #4a4a4a;
    --backdrop: #ecebe8;
  }
  * { margin: 0; padding: 0; box-sizing: border-box; }
  html, body {
    width: 1200px; height: 780px; overflow: hidden;
    background: var(--backdrop);
    font-family: "Mulish", sans-serif;
  }
  .sheet {
    width: 1200px; height: 780px;
    display: flex; align-items: center; justify-content: center; gap: 44px;
  }
  .card {
    position: relative;
    width: 540px; height: 310px;
    border-radius: 18px;
    overflow: hidden;
    box-shadow: 0 8px 22px rgba(0,0,0,0.18);
  }

  /* Front */
  .card-front {
    background: radial-gradient(ellipse at 60% 30%, var(--blue-light) 0%, var(--blue-main) 45%, var(--blue-deep) 100%);
    display: flex; flex-direction: column; align-items: center; justify-content: center;
    color: #fff;
  }
  .brand {
    display: flex; align-items: center; gap: 14px;
    white-space: nowrap;
  }
  .brand-dot {
    flex: 0 0 auto;
    width: 46px; height: 46px; border-radius: 50%;
    background: #fff;
  }
  .brand-name {
    font-weight: 800; font-size: 36px; letter-spacing: -0.5px; line-height: 1;
  }
  .tagline {
    margin-top: 14px; font-size: 19px; font-weight: 400; letter-spacing: 0.3px;
    white-space: nowrap;
  }

  /* Back */
  .card-back {
    background: linear-gradient(160deg, #ffffff 0%, var(--paper) 55%, var(--paper-shade) 100%);
  }
  .back-wave { position: absolute; left: 0; bottom: 0; width: 540px; height: 310px; }
  .back-logo {
    position: absolute; left: 28px; top: 40px;
  }
  .card-back .brand { gap: 9px; }
  .card-back .brand-dot { width: 28px; height: 28px; background: var(--blue-light); }
  .card-back .brand-name { font-size: 21px; color: var(--blue-main); letter-spacing: -0.3px; }
  .card-back .tagline { margin-top: 10px; margin-left: 37px; font-size: 14px; color: var(--blue-deep); }
  .divider {
    position: absolute; left: 280px; top: 34px; width: 1px; height: 170px;
    background: linear-gradient(to bottom, transparent, #e6c99a, transparent);
  }
  .details {
    position: absolute; left: 302px; top: 34px; color: var(--ink);
    white-space: nowrap;
  }
  .person-name { font-size: 22px; font-weight: 800; color: var(--blue-light); }
  .person-title { font-size: 14px; margin-top: 2px; }
  .address { margin-top: 14px; font-size: 13px; line-height: 1.45; }
  .contact-list { list-style: none; margin-top: 10px; font-size: 13px; line-height: 1.55; }
  .contact-list li { display: flex; align-items: center; gap: 8px; }
  .contact-icon {
    flex: 0 0 auto;
    width: 15px; height: 15px; border-radius: 3px; background: var(--blue-main);
    display: inline-flex; align-items: center; justify-content: center;
  }
</style>
</head>
<body>
<main class="sheet">

  <section class="card card-front" aria-label="Card front">
    <div class="brand">
      <span class="brand-dot"></span>
      <span class="brand-name">Tall Pine Computing</span>
    </div>
    <p class="tagline">rooted in computing</p>
  </section>

  <section class="card card-back" aria-label="Card back">
    <svg class="back-wave" viewBox="0 0 540 310" preserveAspectRatio="none" aria-hidden="true">
      <path d="M0 212 C 120 200, 230 236, 330 268 C 410 294, 480 304, 540 300 L540 310 L0 310 Z" fill="var(--orange)"/>
      <path d="M0 222 C 120 210, 230 246, 330 276 C 410 300, 480 308, 540 306 L540 310 L0 310 Z" fill="var(--blue-main)"/>
    </svg>

    <div class="back-logo">
      <div class="brand">
        <span class="brand-dot"></span>
        <span class="brand-name">Tall Pine Computing</span>
      </div>
      <p class="tagline">rooted in computing</p>
    </div>

    <div class="divider"></div>

    <div class="details">
      <p class="person-name">Employee Name</p>
      <p class="person-title">Director</p>
      <p class="address">P.O. Box 000<br>Cedar Ridge, 2nd Land, USA</p>
      <ul class="contact-list">
        <li>
          <span class="contact-icon">
            <svg width="9" height="9" viewBox="0 0 24 24"><path fill="#fff" d="M6.6 10.8a15 15 0 0 0 6.6 6.6l2.2-2.2c.3-.3.7-.4 1-.2 1.1.4 2.3.6 3.6.6.6 0 1 .4 1 1V20c0 .6-.4 1-1 1A17 17 0 0 1 3 4c0-.6.4-1 1-1h3.5c.6 0 1 .4 1 1 0 1.3.2 2.5.6 3.6.1.3 0 .7-.2 1z"/></svg>
          </span>
          0123 456 789
        </li>
        <li>
          <span class="contact-icon">
            <svg width="9" height="9" viewBox="0 0 24 24"><path fill="#fff" d="M2 5h20v14H2z"/><path fill="none" stroke="#1a93d3" stroke-width="2" d="M2 6l10 7 10-7"/></svg>
          </span>
          your@mailbox.net.au
        </li>
        <li>
          <span class="contact-icon">
            <svg width="9" height="9" viewBox="0 0 24 24"><circle cx="12" cy="12" r="9" fill="none" stroke="#fff" stroke-width="2"/><path d="M3 12h18M12 3c3 3 3 15 0 18M12 3c-3 3-3 15 0 18" fill="none" stroke="#fff" stroke-width="1.6"/></svg>
          </span>
          www.yourcompanyweb.com
        </li>
      </ul>
    </div>
  </section>

</main>
</body>
</html>
```